Werbebrief
Zielgruppe
Unsere Zielgruppe sind Geschäftsführer junger Unternehmen.
Hallo,
Wir benötigen einen "Werbebrief". Es ist jedoch weniger ein Brief, als viel mehr eine etwas größerer "Werbekarte" (diese soll 105 x 210mm groß sein).
Auf der Vorderseite soll folgender Text stehen:
Für Unternehmen, die gerne expandieren möchten
Auf der Rückseite soll folgender Link stehen:
www.feldrok-studio.de/Expandieren
Darunter soll folgendes stehen:
Ihr persönlicher Code: ABC123
Wichtig ist, dass wir den Code individuell ändern können, da jeder einen anderen Code bekommt.
Unser Logo und Corporate Farbe habe ich hochgeladen. Das Design sollte auf jeden Fall zu unserer Webseite passen (www.feldrok-studio.de)
Wir freuen uns auf Ihre Vorschläge.

```html
<!DOCTYPE html>
<html lang="de">
<head>
<meta charset="utf-8">
<title>Feldrok Studio – Werbekarte</title>
<link rel="stylesheet" href="https://fonts.googleapis.com/css2?family=Arimo:ital,wght@0,400;0,700;1,700&display=swap">
<style>
  :root {
    --page-bg: #a3a3a3;
    --brand-navy: #044a83;
    --brand-blue: #246397;
    --brand-green: #4aa142;
    --text-light: #ffffff;
    --text-dark: #000000;
    --code-border: #7b7b7b;
  }
  html, body {
    margin: 0;
    padding: 0;
    width: 1200px;
    height: 1200px;
    overflow: hidden;
    background: var(--page-bg);
    font-family: "Arimo", Arial, sans-serif;
  }
  .canvas {
    position: relative;
    width: 1200px;
    height: 1200px;
  }
  .card {
    position: absolute;
    left: 238px;
    width: 714px;
    height: 357px;
    background: var(--brand-blue);
    overflow: hidden;
  }
  .card--front { top: 205px; }
  .card--back  { top: 636px; }

  .card__header {
    position: absolute;
    left: 0; top: 0;
    width: 100%;
    height: 61px;
    background: var(--brand-navy);
    border-bottom: 2px solid #1d5688;
    display: flex;
    align-items: center;
    padding-left: 16px;
    box-sizing: border-box;
    gap: 12px;
  }
  .brand__dot {
    width: 16px;
    height: 16px;
    border-radius: 50%;
    background: var(--text-light);
  }
  .brand__name {
    color: var(--text-light);
    font-size: 30px;
    font-weight: 400;
    letter-spacing: 0.2px;
  }
  .card__footer {
    position: absolute;
    left: 0; bottom: 0;
    width: 100%;
    height: 59px;
    background: var(--brand-green);
    border-top: 2px solid #1f4f6e;
  }

  .headline {
    position: absolute;
    left: 0;
    top: 124px;
    width: 100%;
    margin: 0;
    text-align: center;
    color: var(--text-light);
    font-size: 43px;
    font-weight: 400;
    line-height: 58px;
  }
  .headline__accent {
    font-weight: 700;
    font-style: italic;
    font-size: 56px;
    line-height: 0;
  }

  .back__url {
    position: absolute;
    left: 0;
    top: 134px;
    width: 100%;
    text-align: center;
    color: var(--text-light);
    font-size: 23px;
  }
  .back__code-line {
    position: absolute;
    left: 0;
    top: 168px;
    width: 100%;
    display: flex;
    justify-content: center;
    align-items: center;
    gap: 12px;
    color: var(--text-light);
    font-size: 31px;
  }
  .code-field {
    display: inline-block;
    width: 143px;
    height: 30px;
    line-height: 30px;
    background: var(--text-light);
    border: 1px solid var(--code-border);
    box-sizing: border-box;
    color: var(--text-dark);
    font-size: 20px;
    text-align: center;
  }
</style>
</head>
<body>
<main class="canvas">
  <section class="card card--front" aria-label="Vorderseite">
    <header class="card__header">
      <span class="brand__dot"></span>
      <span class="brand__name">Feldrok Studio</span>
    </header>
    <h1 class="headline">Für Unternehmen, die gerne<br>e<span class="headline__accent">X</span>pandieren möchten</h1>
    <div class="card__footer"></div>
  </section>

  <section class="card card--back" aria-label="Rückseite">
    <header class="card__header">
      <span class="brand__dot"></span>
      <span class="brand__name">Feldrok Studio</span>
    </header>
    <p class="back__url" style="margin:0">www.feldrok-studio.de/Expandieren</p>
    <p class="back__code-line" style="margin:0">
      <span>Ihr persönlicher Code:</span>
      <span class="code-field">ABC123</span>
    </p>
    <div class="card__footer"></div>
  </section>
</main>
</body>
</html>
```